Telecommunications Company needs a business card design

We are looking for a sleek, professional and modern business card design based off our new logo. Will look at both light and dark options. On some designs please provide a small space for a QR code

Target Market(s)

B2B clients in Australia

Contact Information for Business Card

Name, Position, Brisbane (head) office, Phone number, email address, QR code (link to our website qlinetelecom.com.au

Colors
0054AA
0677BA
7BADD7
CADEEF
E8F1F8
0094D4
00A9DD
6FCCEA
C7EBF8
E9F6FB
00AB8E
00BBA5
67D7C9
C6EFE9
E9F9F6

```html
<!DOCTYPE html>
<html lang="en">
<head>
<meta charset="UTF-8">
<title>Qline Telecom – Business Card</title>
<link href="https://fonts.googleapis.com/css2?family=Montserrat:wght@400;500;700&display=swap" rel="stylesheet">
<style>
  :root {
    --backdrop: #141415;
    --card: #1d1d1f;
    --brand-blue: #0677BA;
    --brand-bright: #0094D4;
    --text-light: #f2f2f2;
    --text-muted: #9aa0a8;
  }
  * { margin: 0; padding: 0; box-sizing: border-box; }
  html, body {
    width: 1200px; height: 900px; overflow: hidden;
    background: var(--backdrop);
    font-family: "Montserrat", Arial, sans-serif;
  }
  .stage {
    position: relative; width: 1200px; height: 900px;
  }
  .card {
    position: absolute; left: 250px; width: 700px; height: 400px;
    background: var(--card);
    border-bottom: 7px solid var(--brand-blue);
    box-shadow: 0 18px 40px rgba(0,0,0,.55);
  }
  .card--back { top: 30px; }
  .card--front { top: 470px; }

  .card--back .wordmark {
    position: absolute; inset: 0 0 7px 0;
    display: flex; align-items: center; justify-content: center; gap: 22px;
  }
  .wordmark__dot {
    width: 34px; height: 34px; border-radius: 50%;
    background: var(--brand-bright);
  }
  .wordmark__name {
    font-weight: 700; font-size: 64px; letter-spacing: 1px;
    color: var(--brand-bright);
  }

  .front-brand {
    position: absolute; left: 40px; top: 150px; width: 290px;
    display: flex; align-items: center; gap: 12px;
  }
  .front-brand .wordmark__dot { width: 22px; height: 22px; flex: none; }
  .front-brand .wordmark__name { font-size: 36px; letter-spacing: 0; }

  .divider {
    position: absolute; left: 348px; top: 110px;
    width: 3px; height: 180px; background: var(--brand-blue);
  }

  .details {
    position: absolute; left: 378px; top: 112px; color: var(--text-light);
  }
  .details__name {
    font-weight: 700; font-size: 25px; text-transform: uppercase;
    color: var(--brand-blue); letter-spacing: .5px; line-height: 1;
  }
  .details__role { font-size: 19px; margin-top: 4px; }
  .details__office { font-size: 18px; margin-top: 18px; }
  .contact { list-style: none; margin-top: 10px; }
  .contact li {
    display: flex; align-items: center; gap: 10px;
    font-size: 18px; line-height: 30px;
  }
  .contact svg { width: 16px; height: 16px; flex: none; }
</style>
</head>
<body>
<main class="stage">
  <section class="card card--back" aria-label="Card back">
    <div class="wordmark">
      <span class="wordmark__dot"></span>
      <span class="wordmark__name">Qline Telecom</span>
    </div>
  </section>

  <section class="card card--front" aria-label="Card front">
    <div class="front-brand wordmark">
      <span class="wordmark__dot"></span>
      <span class="wordmark__name">Qline Telecom</span>
    </div>
    <div class="divider"></div>
    <div class="details">
      <p class="details__name">Mark Ellison</p>
      <p class="details__role">Director</p>
      <p class="details__office">Brisbane (head) office</p>
      <ul class="contact">
        <li>
          <svg viewBox="0 0 24 24" fill="none" stroke="#0677BA" stroke-width="2"><path d="M5 3h4l2 5-3 2a11 11 0 0 0 6 6l2-3 5 2v4a2 2 0 0 1-2 2A17 17 0 0 1 3 5a2 2 0 0 1 2-2z"/></svg>
          (07) 3184 5521
        </li>
        <li>
          <svg viewBox="0 0 24 24" fill="none" stroke="#0677BA" stroke-width="2"><rect x="3" y="5" width="18" height="14" rx="1"/><path d="M3 6l9 7 9-7"/></svg>
          qlinetelecom.com.au
        </li>
        <li>
          <svg viewBox="0 0 24 24" fill="none" stroke="#0677BA" stroke-width="2"><circle cx="12" cy="12" r="9"/><path d="M3 12h18M12 3c3 3 3 15 0 18M12 3c-3 3-3 15 0 18"/></svg>
          qlinetelecom.com.au
        </li>
      </ul>
    </div>
  </section>
</main>
</body>
</html>
```